American cannabis tech company business card design

Pavrel.com is seeking a modern, professional, and brand-aligned business card that represents our company and its core values: Mission, Story, Values, and Impact. As an innovative cannabis company, we want a business card that is not only visually appealing but also serves as a representation of who we are and what we stand for.

Project Scope: Design a double-sided business card that integrates our brand identity and core values. Incorporate our key brand elements, ensuring a sleek and contemporary aesthetic. Visually reflect our core values (Mission, Story, Values, Impact) in a way that is engaging yet professional.

Target Market(s)

Vendors, third parties,

Contact Information for Business Card

Contact details (name, title, email, phone, website, etc.)

Font styles to use
Other font styles liked:
• Caslon, Centra

Colors

Designer to choose colors to be used in the design.

Requirements
Must have
• Pavrel.com logo and branding A creative yet clean way to integrate our core values (Mission, Story, Values, Impact) Modern typography and a well-structured layout
Nice to have
• forest green, grey, white, black
Should not have
• references to marijuana, leafs, plants, or related product

```html
<!DOCTYPE html>
<html lang="en">
<head>
<meta charset="utf-8">
<title>Pavrel Business Card</title>
<link href="https://fonts.googleapis.com/css2?family=Jost:wght@400;500;700&display=swap" rel="stylesheet">
<style>
  :root {
    --forest: #173419;
    --sage: #4c7a50;
    --paper: #ffffff;
    --paper-shade: #ececec;
    --ink: #3f3f3f;
    --stage: #3b3b3b;
  }
  * { margin: 0; padding: 0; box-sizing: border-box; }
  html, body { width: 1200px; height: 900px; overflow: hidden; }
  body {
    background: var(--stage);
    font-family: "Jost", sans-serif;
    position: relative;
  }
  .card {
    position: absolute;
    left: 280px;
    width: 640px;
    height: 366px;
    background: linear-gradient(135deg, var(--paper) 0%, var(--paper) 45%, var(--paper-shade) 100%);
    overflow: hidden;
  }
  .card--front { top: 52px; }
  .card--back { top: 478px; }

  .brand-name {
    position: absolute;
    color: var(--forest);
    font-weight: 700;
    letter-spacing: 2px;
    line-height: 1;
  }
  .card--front .brand-name { left: 0; right: 0; top: 120px; text-align: center; font-size: 96px; }
  .card--back .brand-name { left: 44px; top: 96px; font-size: 62px; }

  .band-light {
    position: absolute;
    bottom: 0;
    height: 24px;
    background: var(--sage);
  }
  .card--front .band-light { left: 0; right: 0; }
  .card--back .band-light { left: 0; right: 0; }

  .web-tab {
    position: absolute;
    bottom: 0;
    height: 56px;
    background: var(--forest);
    color: var(--paper);
    font-size: 17px;
    font-weight: 500;
    letter-spacing: 4px;
    display: flex;
    align-items: center;
  }
  .card--front .web-tab {
    left: 0; width: 300px;
    padding-left: 30px;
    clip-path: polygon(0 0, 86% 0, 100% 100%, 0 100%);
  }
  .card--back .web-tab {
    right: 0; bottom: 24px; width: 220px; height: 52px;
    justify-content: flex-end;
    padding-right: 26px;
    clip-path: polygon(0 0, 100% 0, 100% 100%, 10% 100%);
  }

  .rule {
    position: absolute;
    height: 1px;
    background: var(--sage);
  }
  .rule--top { left: 300px; right: 28px; top: 92px; }
  .rule--bottom { left: 44px; right: 250px; top: 250px; }

  .contact-list {
    position: absolute;
    right: 26px;
    top: 110px;
    list-style: none;
    color: var(--ink);
    font-size: 18px;
    text-align: right;
    line-height: 30px;
  }
  .contact-list li { display: flex; justify-content: flex-end; align-items: center; gap: 8px; }
  .contact-list svg { width: 16px; height: 16px; fill: var(--forest); }

  .person { position: absolute; left: 44px; top: 262px; }
  .person-name { color: var(--forest); font-size: 24px; font-weight: 500; letter-spacing: 0.5px; }
  .person-title { color: var(--ink); font-size: 17px; }
</style>
</head>
<body>
  <section class="card card--front">
    <div class="brand-name">PAVREL</div>
    <div class="band-light"></div>
    <div class="web-tab">www.pavrel.com</div>
  </section>

  <section class="card card--back">
    <div class="brand-name">PAVREL</div>
    <div class="rule rule--top"></div>
    <ul class="contact-list">
      <li>000-000-0000
        <svg viewBox="0 0 24 24" aria-hidden="true"><path d="M6.6 10.8a15 15 0 0 0 6.6 6.6l2.2-2.2c.3-.3.7-.4 1-.2 1.1.4 2.3.6 3.6.6.6 0 1 .4 1 1V20c0 .6-.4 1-1 1C10.6 21 3 13.4 3 4c0-.6.4-1 1-1h3.5c.6 0 1 .4 1 1 0 1.3.2 2.5.6 3.6.1.3 0 .7-.2 1z"/></svg>
      </li>
      <li>nolan@pavrel.com
        <svg viewBox="0 0 24 24" aria-hidden="true"><path d="M2 5h20v14H2z M3.5 6.5 12 13l8.5-6.5" fill="none" stroke="#173419" stroke-width="2"/></svg>
      </li>
    </ul>
    <div class="rule rule--bottom"></div>
    <div class="person">
      <div class="person-name">NOLAN REEVE</div>
      <div class="person-title">Co-founder &amp; CEO</div>
    </div>
    <div class="web-tab">www.pavrel.com</div>
    <div class="band-light"></div>
  </section>
</body>
</html>
```